Request for Business Card Design

Hi. My name is Marlene, I am looking for a new business card design for my company, Quarrow Signal Instruments, LLC. I really like the design you did for Tarsel Venture and was hoping you could do something similar using our full logo and our mark. I am also open to any raised texture design using our mark. I have attached our full logo, which would need to be somewhere on the card, as well as the mark in both outline and full form, as well as our brand colors / guide. The card does not have to be white, as long as our logo and mark appear. I actually like darker colored business cards more, but am open to all options. If you are interested in working with me, please let me know. We would also take the business card design into letterhead design if you can do that.

```html
<!DOCTYPE html>
<html lang="en">
<head>
<meta charset="utf-8">
<title>Quarrow Signal Instruments — Business Card</title>
<link href="https://fonts.googleapis.com/css2?family=Saira:wght@700&family=Arimo:ital,wght@0,400;0,700;1,400&display=swap" rel="stylesheet">
<style>
  :root {
    --backdrop: #0e0e0f;
    --card: #232323;
    --brand-blue: #0a8fba;
    --text-light: #f2f2f2;
    --mark-shadow: #161616;
  }
  * { margin: 0; padding: 0; box-sizing: border-box; }
  html, body {
    width: 1200px; height: 963px; overflow: hidden;
    background: var(--backdrop);
  }
  .sheet {
    width: 1200px; height: 963px;
    display: flex; flex-direction: column; align-items: center; justify-content: center; gap: 40px;
  }
  .card {
    position: relative;
    width: 720px; height: 411px;
    background: var(--card);
    border-radius: 28px;
    border-bottom: 3px solid var(--brand-blue);
    border-right: 3px solid var(--brand-blue);
    overflow: hidden;
  }
  .wordmark {
    display: flex; align-items: center; gap: 22px;
    font-family: "Saira", sans-serif; font-weight: 700; color: var(--text-light);
  }
  .wordmark-dot {
    width: 74px; height: 74px; border-radius: 50%;
    background: var(--brand-blue);
  }
  .wordmark-name { line-height: 1; letter-spacing: 0.14em; text-transform: uppercase; }
  .wordmark-name .primary { display: block; font-size: 62px; }
  .wordmark-name .secondary { display: block; font-size: 17px; letter-spacing: 0.08em; margin-top: 6px; }

  .card--back { display: flex; align-items: center; justify-content: center; }

  .card--front .wordmark { position: absolute; left: 60px; top: 46px; }
  .card--front .wordmark-name .primary { font-size: 46px; }
  .card--front .wordmark-name .secondary { font-size: 13px; }

  .contact {
    position: absolute; left: 60px; top: 170px;
    font-family: "Arimo", sans-serif; color: var(--text-light);
    font-size: 18px; line-height: 1.45;
  }
  .contact .address { margin-bottom: 10px; }
  .contact ul { list-style: none; }
  .contact li { display: flex; align-items: center; gap: 12px; }
  .contact svg { width: 16px; height: 16px; flex: none; }

  .holder {
    position: absolute; right: 70px; top: 60px; text-align: right;
    font-family: "Arimo", sans-serif;
  }
  .holder-name { color: var(--brand-blue); font-weight: 700; font-size: 26px; letter-spacing: 0.04em; text-transform: uppercase; }
  .holder-role { color: var(--text-light); font-style: italic; font-size: 20px; margin-top: 4px; }
  .edge-tab {
    position: absolute; right: 0; top: 64px;
    width: 36px; height: 52px; background: var(--brand-blue);
  }
  .raised-disc {
    position: absolute; right: 150px; bottom: -90px;
    width: 330px; height: 330px; border-radius: 50%;
    background: radial-gradient(circle at 35% 80%, #3a3a3a 0%, var(--mark-shadow) 55%, #121212 100%);
  }
</style>
</head>
<body>
<main class="sheet">
  <section class="card card--back" aria-label="Card back">
    <div class="wordmark">
      <span class="wordmark-dot"></span>
      <span class="wordmark-name"><span class="primary">Quarrow</span><span class="secondary">Signal Instruments</span></span>
    </div>
  </section>

  <section class="card card--front" aria-label="Card front">
    <div class="raised-disc" role="img" aria-label="Raised spot-gloss brand mark"></div>
    <div class="wordmark">
      <span class="wordmark-name"><span class="primary">Quarrow</span><span class="secondary">Signal Instruments</span></span>
    </div>
    <div class="holder">
      <p class="holder-name">Elias Morrow</p>
      <p class="holder-role">Manager</p>
    </div>
    <div class="edge-tab"></div>
    <div class="contact">
      <p class="address">Your Address, City<br>State, Zip 0000</p>
      <ul>
        <li><svg viewBox="0 0 16 16"><path d="M4 1.5l2.2 3-1.3 1.6c.9 2 2.2 3.3 4.2 4.2l1.6-1.3 3 2.2-1.2 2.6C7 13.5 2.5 9 1.5 2.7z" fill="#0a8fba"/></svg>123-456-2100</li>
        <li><svg viewBox="0 0 16 16"><rect x="1.5" y="3.5" width="13" height="9" fill="none" stroke="#0a8fba" stroke-width="1.3"/><path d="M1.5 3.5l6.5 5 6.5-5" fill="none" stroke="#0a8fba" stroke-width="1.3"/></svg>youremail@mailbox.com</li>
        <li><svg viewBox="0 0 16 16" fill="none" stroke="#0a8fba" stroke-width="1.2"><circle cx="8" cy="8" r="6.3"/><ellipse cx="8" cy="8" rx="2.8" ry="6.3"/><path d="M1.7 8h12.6M2.8 4.6h10.4M2.8 11.4h10.4"/></svg>www.yourwebsite.com</li>
      </ul>
    </div>
  </section>
</main>
</body>
</html>
```